Corvane Capital Business Cards

These are professional business cards that are for my family office.
Put fake emails and phone numbers as of now until I finalize those components. This family office controls my families investments, assets, and future. The cards should be professional.
..
.
.
.
I just uploaded another variation of a logo I would like to see as a business card to I am inbeteen which logo to use

Target Market(s)

business

Industry/Entity Type

business

Contact Information for Business Card

Professional, wealth related, finance related.

Requirements
Must have
• Logo

```html
<!DOCTYPE html>
<html lang="en">
<head>
<meta charset="utf-8">
<title>Corvane Capital Business Cards</title>
<link rel="stylesheet" href="https://fonts.googleapis.com/css2?family=Cinzel:wght@500&family=Montserrat:wght@400;600&display=swap">
<style>
  :root {
    --canvas: #e8e5e0;
    --card: #1a1f2b;
    --emblem: #262d3d;
    --white: #ffffff;
    --grey: #a9abaf;
    --light: #d6d8dc;
    --deboss: #2c3345;
  }
  * { margin: 0; padding: 0; box-sizing: border-box; }
  html, body { width: 900px; height: 1200px; overflow: hidden; }
  body { background: var(--canvas); position: relative; font-family: "Montserrat", sans-serif; }

  .card {
    position: absolute;
    background: var(--card);
    border-radius: 24px;
    overflow: hidden;
  }
  .card--front { left: 80px; top: 130px; width: 742px; height: 442px; }
  .card--back  { left: 78px; top: 638px; width: 744px; height: 442px; }

  .emblem-area {
    position: absolute;
    left: 445px;
    top: -5px;
    width: 460px;
    height: 460px;
    border-radius: 50%;
    background: var(--emblem);
  }

  .wordmark {
    position: absolute;
    font-family: "Cinzel", serif;
    font-weight: 500;
    white-space: nowrap;
  }
  .card--front .wordmark { left: 36px; top: 66px; font-size: 37px; color: var(--white); letter-spacing: 0.3px; }
  .card--back .wordmark  { left: 72px; top: 196px; font-size: 61px; color: var(--deboss); letter-spacing: 1px; }

  .holder { position: absolute; left: 37px; top: 188px; }
  .holder__name { font-size: 26px; font-weight: 600; color: var(--grey); line-height: 1.1; }
  .holder__title { font-size: 16px; color: var(--light); margin-top: 4px; }

  .address { position: absolute; left: 38px; top: 268px; font-size: 16px; line-height: 21px; color: var(--light); font-style: normal; }

  .contacts { position: absolute; left: 38px; top: 328px; list-style: none; }
  .contacts li { display: flex; align-items: center; height: 28px; font-size: 16px; color: var(--light); }
  .contacts svg { width: 15px; height: 15px; margin-right: 10px; fill: var(--grey); }
</style>
</head>
<body>

  <section class="card card--front" aria-label="Business card front">
    <div class="emblem-area" role="img" aria-label="Large circular brand emblem"></div>

    <div class="wordmark">Corvane Capital</div>

    <div class="holder">
      <div class="holder__name">Martin Ellery</div>
      <div class="holder__title">Owner</div>
    </div>

    <address class="address">
      42 Harborview Court<br>
      Lindenfield, NJ 07112 USA
    </address>

    <ul class="contacts">
      <li>
        <svg viewBox="0 0 16 16" aria-hidden="true"><path d="M3.6 1.2l2.3 2.6-1.2 1.9c.9 2 2.5 3.6 4.6 4.6l1.9-1.2 2.6 2.3-1.4 2.4C7.4 13.6 2.4 8.6 1.2 3.6z"/></svg>
        (555)204-7731
      </li>
      <li>
        <svg viewBox="0 0 16 16" aria-hidden="true"><path d="M1 3.5h14v1L8 9 1 4.5zM1 6l7 4.5L15 6v6.5H1z"/></svg>
        info@yourwebsitename.com
      </li>
      <li>
        <svg viewBox="0 0 16 16" aria-hidden="true"><circle cx="8" cy="8" r="7"/></svg>
        www.yourwebsitename.com
      </li>
    </ul>
  </section>

  <section class="card card--back" aria-label="Business card back">
    <div class="wordmark">Corvane Capital</div>
  </section>

</body>
</html>
```